Business Identity Stationary

Already have the logo which is in the attached files so only need the Business STationary
1) Double Sided Business Card
2) Letterhead
3) Presentation folder with business card holder on inside cover
4) WIth compliments slip
See information for business cards, letterhead and presentation folder below.

This should be a simply job using a logo we already had designed along with a little device. I suggest using the device off center and perhaps lower in the corner in an abstract way. Also the logo device could be used as a watermark for the letterhead. The designer who created the logo presented something that I think works well for a business card. The front of the double sided business card could have the name logo small for the website address and only use the Lime device on the front. Then on the back could be the name Barrow Advisory logo.

Please note that for the business card the black and lime green background do look good. Also please think of using the lime device separately in an unusual way.

It has been brought to my attention that.my budget was far to low. Hopefully this.will attract you to the project. 

The parent company of Barrow Advisory is TallHeron holdings. I have uploaded a file of the Tall Heron business card I really like. Perhaps use this business card as a guide to the type of modern and clean style I am looking for. It also works to have the Barrow Advisroy and Tall Heron similar.

Reason: Still haven't received anything exactly right.

Industry/Entity Type

Business

Font styles to use
Sans Serif

Colors
9bcb3c
000000
5c5c5c
add136
cadf82
eaf2cf
f9fbf2
1b1b1b
757575

Requirements
Must have
• 1) Double Sided Business Card
Marta Kellendorf
Director
Tel: +505 8264 3170
Email: mk@barrowadvisory-example.com
Website: www.barrowadvisory-example.com

Frederick Kellendorf
Director
Tel: +505 8264 3172
Email: fk@barrowadvisory-example.com

Lucia Brenes Otaduy
Director
Tel: 8642 1093
Email: lbo@barrowadvisory-example.com

2) Letterhead
Logo
Lime Logo Device
Website Address: www.barrowadvisory-example.com
Small print on bottom: Barrow Advisory a Tall Heron Holding Company SA. RUC J0487000239518

3) Presentation Folder
Traditional Presentation folder with inside front cover spot for the insertion of business card.

4) With Compliments slip

```html
<!DOCTYPE html>
<html lang="en">
<head>
<meta charset="utf-8">
<title>Barrow Advisory — Business Stationery</title>
<link rel="stylesheet" href="https://fonts.googleapis.com/css2?family=Questrial&family=Open+Sans:wght@400;600&display=swap">
<style>
  :root {
    --lime: #86e22a;
    --lime-soft: #eaf2cf;
    --lime-faint: #f2f8e4;
    --ink: #1b1b1b;
    --black: #000000;
    --grey: #5c5c5c;
    --grey-light: #dcdcde;
    --stage: #e6e6e6;
    --paper: #ffffff;
  }
  * { box-sizing: border-box; margin: 0; padding: 0; }
  html, body { width: 1200px; height: 1000px; overflow: hidden; }
  body {
    position: relative;
    background: var(--stage);
    font-family: "Open Sans", Arial, sans-serif;
    color: var(--ink);
  }
  .sheet {
    position: absolute;
    background: var(--paper);
    box-shadow: 3px 3px 4px rgba(0,0,0,.55);
    overflow: hidden;
  }
  .band {
    position: absolute;
    left: 0; right: 0;
    background: linear-gradient(90deg, var(--lime) 0%, #b9f07c 45%, rgba(255,255,255,0) 100%);
  }
  .wordmark {
    position: absolute;
    display: flex;
    align-items: center;
    gap: 5px;
    font-family: "Questrial", "Century Gothic", sans-serif;
    color: var(--black);
    white-space: nowrap;
    line-height: 1;
  }
  .wordmark .dot {
    border-radius: 50%;
    background: var(--lime);
    flex: none;
  }
  .device {
    position: absolute;
    border-radius: 50%;
    background: var(--lime-faint);
  }
  .fine {
    position: absolute;
    left: 0; right: 0;
    text-align: center;
    font-size: 6px;
    font-weight: 600;
    color: var(--ink);
    line-height: 9px;
  }

  /* Letterhead */
  .letterhead { left: 28px; top: 33px; width: 369px; height: 477px; }
  .letterhead .band { top: 51px; height: 6px; }
  .letterhead .wordmark { right: 12px; top: 14px; font-size: 15px; }
  .letterhead .wordmark .dot { width: 10px; height: 10px; }
  .letterhead .watermark { left: 87px; top: 150px; width: 208px; height: 208px; }
  .letterhead .fine.web { top: 456px; }
  .letterhead .fine.legal { top: 465px; }

  /* Presentation folder */
  .folder { left: 428px; top: 33px; width: 752px; height: 477px; }
  .folder .fold { position: absolute; left: 374px; top: 0; bottom: 0; width: 1px; background: #bdbdbd; }
  .folder .band { top: 51px; height: 6px; }
  .folder .wordmark { top: 14px; font-size: 15px; }
  .folder .wordmark .dot { width: 10px; height: 10px; }
  .folder .wordmark.back-panel { right: 390px; }
  .folder .wordmark.front-panel { right: 14px; }
  .folder .fine.web { top: 456px; right: 378px; }
  .folder .fine.legal { top: 465px; right: 378px; }
  .card-holder {
    position: absolute; left: 585px; top: 203px; width: 157px; height: 100px;
    border: 1px solid #777;
  }
  .mini-card {
    position: absolute; left: 4px; top: 3px; width: 147px; height: 92px;
    border: 1px solid #999; background: var(--paper); overflow: hidden;
  }
  .mini-card .band { top: 30px; height: 5px; }
  .mini-card .wordmark { right: 5px; top: 9px; font-size: 9px; gap: 3px; }
  .mini-card .wordmark .dot { width: 6px; height: 6px; }
  .mini-card .name { position: absolute; left: 4px; top: 42px; font-size: 5.5px; color: var(--lime); }
  .mini-card .role { position: absolute; left: 4px; top: 50px; font-size: 5px; color: var(--grey); }
  .mini-card .contact { position: absolute; left: 4px; top: 60px; font-size: 4.5px; line-height: 7px; }
  .mini-card .contact span::before { content: ""; display: inline-block; width: 4px; height: 3px; margin-right: 3px; background: var(--lime); }
  .mini-card .device { right: 4px; bottom: 4px; width: 22px; height: 22px; }

  /* Compliments slip */
  .comp-slip { left: 294px; top: 526px; width: 571px; height: 262px; }
  .comp-slip .band { top: 61px; height: 10px; }
  .comp-slip .wordmark { right: 8px; top: 18px; font-size: 20px; gap: 6px; }
  .comp-slip .wordmark .dot { width: 13px; height: 13px; }
  .comp-slip .greeting { position: absolute; left: 59px; top: 85px; font-size: 8px; font-weight: 600; }
  .comp-slip .web { position: absolute; left: 17px; top: 244px; font-size: 8px; font-weight: 600; }
  .comp-slip .device { right: 10px; bottom: 10px; width: 48px; height: 48px; }

  /* Business cards */
  .card { top: 808px; width: 280px; height: 174px; }
  .card .band { top: 52px; height: 12px; }
  .card-front { left: 25px; }
  .card-front .emblem { position: absolute; left: 127px; top: 8px; width: 34px; height: 34px; border-radius: 50%; background: var(--lime); }
  .card-front .wordmark { left: 0; right: 0; top: 94px; justify-content: center; font-size: 30px; }
  .card-back .wordmark { right: 8px; top: 13px; font-size: 15px; }
  .card-back .wordmark .dot { width: 10px; height: 10px; }
  .card-back .name { position: absolute; left: 8px; top: 80px; font-size: 11px; color: var(--lime); }
  .card-back .role { position: absolute; left: 8px; top: 97px; font-size: 9.5px; color: var(--grey); }
  .card-back .contacts { position: absolute; left: 8px; top: 115px; list-style: none; font-size: 9px; line-height: 14.3px; color: var(--ink); }
  .card-back .contacts li { display: flex; align-items: center; gap: 8px; }
  .card-back .contacts svg { width: 11px; height: 9px; flex: none; }
  .card-back .device { right: 8px; bottom: 10px; width: 50px; height: 50px; }
  .card-b1 { left: 320px; }
  .card-b2 { left: 611px; }
  .card-b3 { left: 902px; }
</style>
</head>
<body>

<!-- Letterhead -->
<section class="sheet letterhead" aria-label="Letterhead">
  <div class="wordmark"><span class="dot"></span>Barrow Advisory</div>
  <div class="band"></div>
  <div class="device watermark" role="img" aria-label="Faint brand device watermark"></div>
  <p class="fine web">www.barrowadvisory-example.com</p>
  <p class="fine legal">Barrow Advisory a Tall Heron Holding Company SA. RUC J0487000239518</p>
</section>

<!-- Presentation folder -->
<section class="sheet folder" aria-label="Presentation folder">
  <div class="band"></div>
  <div class="fold"></div>
  <div class="wordmark back-panel"><span class="dot"></span>Barrow Advisory</div>
  <div class="wordmark front-panel"><span class="dot"></span>Barrow Advisory</div>
  <p class="fine web" style="left:0;">www.barrowadvisory-example.com</p>
  <p class="fine legal" style="left:0;">Barrow Advisory a Tall Heron Holding Company SA. RUC J0487000239518</p>
  <div class="card-holder">
    <div class="mini-card">
      <div class="wordmark"><span class="dot"></span>Barrow Advisory</div>
      <div class="band"></div>
      <p class="name">Marta Kellendorf</p>
      <p class="role">Director</p>
      <p class="contact"><span>mk@barrowadvisory-example.com</span><br><span>+505 8264 3170</span><br><span>www.barrowadvisory-example.com</span></p>
      <div class="device" role="img" aria-label="Brand device"></div>
    </div>
  </div>
</section>

<!-- With compliments slip -->
<section class="sheet comp-slip" aria-label="With compliments slip">
  <div class="wordmark"><span class="dot"></span>Barrow Advisory</div>
  <div class="band"></div>
  <p class="greeting">With Compliments,</p>
  <p class="web">www.barrowadvisory-example.com</p>
  <div class="device" role="img" aria-label="Brand device"></div>
</section>

<!-- Business card front -->
<section class="sheet card card-front" aria-label="Business card front">
  <div class="emblem"></div>
  <div class="band"></div>
  <div class="wordmark">Barrow Advisory</div>
</section>

<!-- Business card backs -->
<section class="sheet card card-back card-b1" aria-label="Business card back">
  <div class="wordmark"><span class="dot"></span>Barrow Advisory</div>
  <div class="band"></div>
  <p class="name">Marta Kellendorf</p>
  <p class="role">Director</p>
  <ul class="contacts">
    <li><svg viewBox="0 0 11 9"><rect width="11" height="9" fill="#86e22a"/><path d="M0 0 L5.5 5 L11 0" stroke="#fff" fill="none"/></svg>mk@barrowadvisory-example.com</li>
    <li><svg viewBox="0 0 11 9"><rect x="3" y="0" width="5" height="9" rx="1" fill="#86e22a"/><rect x="4" y="1" width="3" height="4" fill="#fff"/></svg>+505 8264 3170</li>
    <li><svg viewBox="0 0 11 9"><circle cx="5.5" cy="4.5" r="4.5" fill="#86e22a"/><path d="M1 4.5 H10 M5.5 0 V9" stroke="#fff" stroke-width=".8"/></svg>www.barrowadvisory-example.com</li>
  </ul>
  <div class="device" role="img" aria-label="Brand device"></div>
</section>

<section class="sheet card card-back card-b2" aria-label="Business card back">
  <div class="wordmark"><span class="dot"></span>Barrow Advisory</div>
  <div class="band"></div>
  <p class="name">Frederick Kellendorf</p>
  <p class="role">Director</p>
  <ul class="contacts">
    <li><svg viewBox="0 0 11 9"><rect width="11" height="9" fill="#86e22a"/><path d="M0 0 L5.5 5 L11 0" stroke="#fff" fill="none"/></svg>fk@barrowadvisory-example.com</li>
    <li><svg viewBox="0 0 11 9"><rect x="3" y="0" width="5" height="9" rx="1" fill="#86e22a"/><rect x="4" y="1" width="3" height="4" fill="#fff"/></svg>+505 8264 3172</li>
    <li><svg viewBox="0 0 11 9"><circle cx="5.5" cy="4.5" r="4.5" fill="#86e22a"/><path d="M1 4.5 H10 M5.5 0 V9" stroke="#fff" stroke-width=".8"/></svg>www.barrowadvisory-example.com</li>
  </ul>
  <div class="device" role="img" aria-label="Brand device"></div>
</section>

<section class="sheet card card-back card-b3" aria-label="Business card back">
  <div class="wordmark"><span class="dot"></span>Barrow Advisory</div>
  <div class="band"></div>
  <p class="name">Lucia Brenes Otaduy</p>
  <p class="role">Director</p>
  <ul class="contacts">
    <li><svg viewBox="0 0 11 9"><rect width="11" height="9" fill="#86e22a"/><path d="M0 0 L5.5 5 L11 0" stroke="#fff" fill="none"/></svg>lbo@barrowadvisory-example.com</li>
    <li><svg viewBox="0 0 11 9"><rect x="3" y="0" width="5" height="9" rx="1" fill="#86e22a"/><rect x="4" y="1" width="3" height="4" fill="#fff"/></svg>+505 8642 1093</li>
    <li><svg viewBox="0 0 11 9"><circle cx="5.5" cy="4.5" r="4.5" fill="#86e22a"/><path d="M1 4.5 H10 M5.5 0 V9" stroke="#fff" stroke-width=".8"/></svg>www.barrowadvisory-example.com</li>
  </ul>
  <div class="device" role="img" aria-label="Brand device"></div>
</section>

</body>
</html>
```